Refresh of far from plain IT company website

Our web site is starting to show it's age. You can see the existing site here: www.plumbwick.net. As a growing company we want to come across as a dynamic collection of IT experts.

We want to update the design so are open to any colour palette and look, but want to retain our current table logo. We use the logo on our business cards but with a white background - see the attached file, so you don't need to keep the brown or the green.

The design should consider the range of browsers that will be looking at the site - so please show how it will look on a wide screen laptop and a 768x1024 tablet.

We want to add some pages about our team and their skills, probably with photos of each person on the team.

This is an uncoded project - the PSD files of the design is required, not coding.
Updates

Thanks everyone for the submissions so far.  It's a holiday day in the UK today but we will get some feedback on the designs so far out to you.

Target Market(s)

Architects and other creative types looking for IT support

Industry/Entity Type

Business

Font styles to use
Serif
Sans Serif

Requirements
Must have
• Must look good on a laptop and an iPad.

```html
<!DOCTYPE html>
<html lang="en">
<head>
<meta charset="utf-8">
<title>plumbwick – Serious IT Support for Business</title>
<link href="https://fonts.googleapis.com/css2?family=Source+Sans+3:wght@400;600;700&display=swap" rel="stylesheet">
<style>
:root{
  --plum:#9a0f52;
  --plum-dark:#8a0845;
  --plum-deep:#7e0740;
  --plum-footer:#a10a55;
  --plum-tab:#b5477c;
  --gold:#d8aa10;
  --gold-light:#f2c51a;
  --ink:#3d3d3d;
  --muted:#6a6a6a;
  --white:#ffffff;
  --rule:#e4e4e4;
}
*{margin:0;padding:0;box-sizing:border-box}
html,body{width:870px;height:1200px;overflow:hidden;background:var(--white)}
body{font-family:"Source Sans 3",Arial,sans-serif;color:var(--ink);position:relative}
.abs{position:absolute}
a{color:inherit;text-decoration:none}

/* header */
.brand{left:92px;top:26px;display:flex;align-items:center;gap:10px;color:var(--plum);font-size:25px;font-weight:700}
.brand-mark{width:14px;height:14px;background:var(--gold)}
.top-links{top:14px;left:626px;display:flex;gap:22px;font-size:12px;color:var(--plum)}

/* nav */
.nav{top:74px;left:0;width:870px;height:37px;background:linear-gradient(#a5205f,var(--plum) 45%,#8c0c4a)}
.nav-item{top:0;height:37px;line-height:37px;color:var(--white);font-size:12px}
.nav-home{left:72px;width:62px;text-align:center;background:var(--plum-tab)}
.remote{left:579px;top:0;width:218px;height:37px;background:var(--plum-tab)}
.remote-label{left:9px;top:0;line-height:37px;color:var(--white);font-size:12px}
.remote-input{left:62px;top:6px;width:124px;height:23px;background:var(--white);color:var(--plum);font-size:12px;line-height:23px;padding-left:10px}
.remote-go{left:186px;top:6px;width:22px;height:23px;background:var(--gold-light);color:var(--plum);font-size:11px;line-height:23px;text-align:center}

/* hero */
.hero-title{top:124px;left:0;width:870px;text-align:center;font-size:20px;color:var(--plum)}
.hero-title span{color:var(--gold)}
.hero-art{left:100px;top:158px;width:700px;height:210px;background:radial-gradient(ellipse at 50% 60%,#c9406f 0%,#e8a9be 35%,#f7e6ec 60%,#ffffff 78%)}
.dots{top:376px;left:407px;display:flex;gap:6px}
.dot{width:9px;height:9px;border-radius:50%;background:#e2e2e2}
.dot.on{background:var(--plum)}
.hero-rule{top:399px;left:110px;width:650px;height:1px;background:linear-gradient(90deg,transparent,var(--rule) 20%,var(--rule) 80%,transparent)}

/* welcome */
.welcome{top:410px;left:0;width:870px;text-align:center;font-size:22px;color:var(--plum)}
.intro{top:442px;left:88px;width:696px;text-align:center;font-size:12px;line-height:15px;color:#4b4b4b}
.btn{display:inline-block;background:var(--plum);color:var(--white);font-size:10px;line-height:20px;height:20px;padding:0 8px;border-radius:4px}
.intro-btn{top:481px;left:406px}

/* services */
.service{top:522px;width:130px;text-align:center}
.service h3{font-weight:400;font-size:11.5px;color:var(--plum);height:22px}
.service p{font-size:9px;line-height:11.3px;color:var(--muted)}
.service-icon{width:56px;height:56px;margin:14px auto 0;border-radius:12px}
.service .btn{margin-top:16px}

/* news + articles */
.section-h{font-size:11.5px;color:var(--plum)}
.date{width:48px;height:48px;border-radius:50%;background:var(--gold);color:var(--white);text-align:center;font-size:14px;line-height:17px;padding-top:7px}
.news-text{width:160px;font-size:9.5px;line-height:11.5px;color:#4b4b4b}
.article-img{left:346px;top:755px;width:163px;height:113px;background:linear-gradient(135deg,#2e3138,#6c7077 55%,#3a3d44)}
.article-title{left:521px;top:756px;width:250px;font-size:13px;line-height:13px;color:var(--plum)}
.article-text{left:521px;top:785px;width:245px;font-size:9.4px;line-height:13px;color:#555}

/* partner band */
.partners{top:914px;left:0;width:870px;height:88px;background:var(--plum-dark);display:flex;align-items:center;justify-content:center;gap:18px;color:var(--white);font-size:13px;font-weight:600}

/* footer */
.footer{top:1002px;left:0;width:870px;height:198px;background:var(--plum-footer)}
.footer-panel{left:575px;top:0;width:207px;height:198px;background:var(--plum-deep)}
.footer-links{left:107px;top:22px;list-style:none;color:var(--white);font-size:11px;line-height:17.5px}
.signup-h{left:277px;top:23px;color:var(--white);font-size:14px}
.signup-input{left:276px;top:51px;width:192px;height:26px;background:var(--white);border-radius:5px;font-size:11px;line-height:26px;padding-left:12px;color:#8b8b8b}
.signup-note{left:280px;top:88px;width:200px;color:var(--white);font-size:8.5px;line-height:11px}
.signup-btn{left:280px;top:120px;width:57px;height:21px;background:var(--gold-light);border-radius:5px;color:var(--plum);font-size:11px;font-weight:700;text-align:center;line-height:21px}
.story{left:569px;top:11px;width:222px;height:145px;background:var(--white);padding:7px 35px}
.story h4{font-size:16px;font-weight:600;color:#111}
.story p{margin-top:9px;font-size:9.6px;line-height:12.2px;color:#111}
.story .author{text-align:right;margin-top:9px;padding-right:0}
.social{left:690px;top:1168px;display:flex;gap:6px}
.social span{width:17px;height:17px;border-radius:3px;background:#c94c86}
</style>
</head>
<body>

<header>
  <div class="abs brand"><span class="brand-mark"></span>plumbwick</div>
  <nav class="abs top-links"><a>Contact</a><a>Support</a><a>Terms</a></nav>
</header>

<div class="abs nav">
  <a class="abs nav-item nav-home">Home</a>
  <a class="abs nav-item" style="left:141px">About us</a>
  <a class="abs nav-item" style="left:206px">What we do</a>
  <a class="abs nav-item" style="left:286px">News blog</a>
  <a class="abs nav-item" style="left:360px">Articles</a>
  <a class="abs nav-item" style="left:417px">Clients</a>
  <a class="abs nav-item" style="left:470px">Partners</a>
  <div class="abs remote">
    <span class="abs remote-label">Remote</span>
    <span class="abs remote-input">Session ID</span>
    <span class="abs remote-go">GO</span>
  </div>
</div>

<h1 class="abs hero-title" style="font-weight:400">Serious IT Support for <span>Business</span></h1>
<div class="abs hero-art" role="img" aria-label="Illustration of three glossy crimson buttons with question mark, exclamation mark and pointing hand, with small white figures on a pink swoosh"></div>
<div class="abs dots"><span class="dot"></span><span class="dot"></span><span class="dot"></span><span class="dot on"></span></div>
<div class="abs hero-rule"></div>

<h2 class="abs welcome" style="font-weight:400">Welcome</h2>
<p class="abs intro">Plumbwick was established with a specific aim: to consistently deliver an advanced and comprehensive IT service for ambitious growing companies across all industry sectors.</p>
<a class="abs btn intro-btn">Read more</a>

<section>
  <div class="abs service" style="left:89px"><h3>IT Support Management</h3><p>Duis aute irure dolor in reprehenderit in voluptate velit esse cillum dolore eu fugiat nulla pariatur.</p><div class="service-icon" role="img" aria-label="Icon of a support agent with headset" style="background:linear-gradient(#d9d9d9,#1f2a48)"></div><a class="btn">Read more</a></div>
  <div class="abs service" style="left:229px"><h3>Cloud Computing</h3><p>Duis aute irure dolor in reprehenderit in voluptate velit esse cillum dolore eu fugiat nulla pariatur.</p><div class="service-icon" role="img" aria-label="Icon of a blue cloud" style="background:linear-gradient(#bfe6fb,#3fa3e0)"></div><a class="btn">Read more</a></div>
  <div class="abs service" style="left:367px"><h3>Disaster Recovery</h3><p>Duis aute irure dolor in reprehenderit in voluptate velit esse cillum dolore eu fugiat nulla pariatur.</p><div class="service-icon" role="img" aria-label="Icon of a cloud with database stack" style="background:linear-gradient(#4aa3e6,#8e8f94)"></div><a class="btn">Read more</a></div>
  <div class="abs service" style="left:512px"><h3>Virtualisation</h3><p>Duis aute irure dolor in reprehenderit in voluptate velit esse cillum dolore eu fugiat nulla pariatur.</p><div class="service-icon" role="img" aria-label="Icon of a globe on a hard drive" style="background:linear-gradient(#2a6fcf,#cfd2d6)"></div><a class="btn">Read more</a></div>
  <div class="abs service" style="left:653px"><h3>CAD Services</h3><p>Duis aute irure dolor in reprehenderit in voluptate velit esse cillum dolore eu fugiat nulla pariatur.</p><div class="service-icon" role="img" aria-label="Icon of a globe with a gear" style="background:radial-gradient(circle,#5aa0e8,#1b3f86)"></div><a class="btn">Read more</a></div>
</section>

<section>
  <h3 class="abs section-h" style="left:93px;top:723px;font-weight:400">News Blogs</h3>
  <div class="abs date" style="left:89px;top:748px">15<br>Jan</div>
  <p class="abs news-text" style="left:142px;top:757px">Duis aute irure dolor in reprehenderit in voluptate velit esse cillum dolore eu fugiat nulla pariatur.</p>
  <div class="abs date" style="left:89px;top:811px">15<br>Jan</div>
  <p class="abs news-text" style="left:142px;top:820px">Duis aute irure dolor in reprehenderit in voluptate velit esse cillum dolore eu fugiat nulla pariatur.</p>
  <a class="abs btn" style="left:237px;top:874px">Read more</a>
</section>

<section>
  <h3 class="abs section-h" style="left:346px;top:729px;font-weight:400">Articles</h3>
  <div class="abs article-img" role="img" aria-label="Photo of a woman using a futuristic touch screen interface"></div>
  <h4 class="abs article-title" style="font-weight:400">Nam libero tempore, cum soluta nobis est eligendi optio</h4>
  <p class="abs article-text">Cumque nihil impedit quo minus id quod maxime placeat facere possimus, omnis voluptas assumenda est, omnis dolor repellendus. Temporibus autem quibusdam et aut officiis debitis aut rerum necessitatibus saepe eveniet ut et voluptates repudiandae sint et molestiae non recusandae. Itaque earum rerum hic tenetur</p>
  <a class="abs btn" style="left:700px;top:875px">Read more</a>
</section>

<div class="abs partners">
  <span>Corvane</span><span>Halden</span><span>Brixmoor</span><span>Tiny Works</span><span>Qarto</span><span>Velmont</span><span>Ashgrove</span><span>Orbelle</span><span>Fieldnote</span><span>Tamsworth</span>
</div>

<footer class="abs footer">
  <div class="abs footer-panel"></div>
  <ul class="abs footer-links">
    <li>Home</li><li>About us</li><li>What we do</li><li>News blog</li><li>Articles</li><li>Clients</li><li>Partners</li>
  </ul>
  <h3 class="abs signup-h" style="font-weight:400">As seen on Daily Ledger</h3>
  <div class="abs signup-input">Enter your email id</div>
  <p class="abs signup-note">Sed ut perspiciatis unde omnis iste natus error sit voluptatem accusantium</p>
  <div class="abs signup-btn">Submit</div>
  <div class="abs story">
    <h4>Success Stories</h4>
    <p>Mauris rhoncus pretium porttitor. Cras scelerisque commodo odio. Phasellus dolor enim, faucibus egestas scelerisque hendrerit, aliquet sed lorem.</p>
    <p class="author">-Author name</p>
  </div>
</footer>
<div class="abs social" aria-label="Social links"><span></span><span></span><span></span><span></span></div>

</body>
</html>
```